Wordpress website for a new Podcast

Hi, We are looking for a designer to create a wordpress website project for a new podcast and publish it on the domain we own.

The show is called “Bright Gatherings” (logo included) and its aim is to interview guests who work as professional facilitators, trainers, teachers and coaches. The show has a positive vibe, is fun, vibrant and full of positive energy. These are the feelings we want to convey in the design.

The website should have a similar structure to: https://www.plumvesselcast.example/ with the following content:

1) The main page including:
- navigation bar and social buttons at the top
- main graphic design featuring the latest episode
- "latest episodes" section displaying 3 episodes (please design a mask to be used for new episodes when they air together with the face of the interviewee) -> this will link to the respective episodes
- please design an "bright gatherings" book cover mockup to be inluded as a banner -> this will link to Orindel
- subscribe to the newsletter - a banner capturing the name and email of the user -> to be connected to PostWren.
-> a working episode search.

2) Episodes page
- the show will be divided into seasons (12 episodes each) and each episode will need a separate "blog entry" including:
-> A short article (4-5 paragraphs) + stock image
-> interviewee's bio and social links

3) Meet the hosts page
- including bios of the two hosts of the show
- links to their social profiles
- a "request speaker availability" form which sends an email

Some additional nice-to-haves:
1) Good and clean Bio's would be awesome (both for the hosts & the interviewees),
2) an easily navigable episode system,
3) a keyword/date search option
4) easy to share options (share to WhatsApp, Facebook, Twitter, LinkedIn) 5) We must be able to track how the podcasts are shared (google analytics?)

```html
<!DOCTYPE html>
<html lang="en">
<head>
<meta charset="utf-8">
<title>Bright Gatherings – Podcast</title>
<link href="https://fonts.googleapis.com/css2?family=Montserrat:wght@600;700;800&family=Open+Sans:wght@400;600;700&display=swap" rel="stylesheet">
<style>
:root{
  --orange:#f04e23;
  --orange-deep:#d8401a;
  --ink:#1d1d1f;
  --night:#161616;
  --footer:#0b0b0b;
  --blush:#f8ede9;
  --muted:#6b6b6b;
  --white:#ffffff;
  --line:#e4e4e4;
}
*{box-sizing:border-box;margin:0;padding:0}
html,body{width:1200px;height:3232px;overflow:hidden}
body{font-family:"Open Sans",Arial,sans-serif;color:var(--ink);background:var(--white);position:relative}
h1,h2,h3,h4,.brand,.btn,.nav a{font-family:"Montserrat",Arial,sans-serif}

/* header */
.site-header{position:absolute;top:0;left:0;width:1200px;height:128px;background:var(--white);z-index:3}
.brand{position:absolute;left:108px;top:6px;width:148px;height:148px;border-radius:50%;background:var(--orange);border:6px solid var(--white);box-shadow:0 4px 10px rgba(0,0,0,.25);display:flex;align-items:center;justify-content:center;text-align:center;color:var(--white);font-weight:800;font-size:20px;line-height:1.1;z-index:4}
.top-contact{position:absolute;left:400px;top:18px;display:flex;gap:40px;font-size:15px;color:var(--ink)}
.top-contact span{display:flex;align-items:center;gap:8px}
.socials{position:absolute;right:116px;top:12px;display:flex;gap:8px}
.socials i{width:36px;height:36px;border-radius:50%;border:2px solid var(--orange);display:block;position:relative}
.socials i.search::before{content:"";position:absolute;left:8px;top:7px;width:12px;height:12px;border:2px solid var(--orange);border-radius:50%}
.socials i.search::after{content:"";position:absolute;left:21px;top:21px;width:7px;height:2px;background:var(--orange);transform:rotate(45deg)}
.nav{position:absolute;left:576px;top:76px;display:flex;gap:30px}
.nav a{text-decoration:none;color:var(--ink);font-size:15px;font-weight:700;text-transform:uppercase;padding-bottom:6px}
.nav a.active{color:var(--orange);border-bottom:2px solid var(--orange)}

/* hero */
.hero{position:absolute;top:128px;left:0;width:1200px;height:690px;background:radial-gradient(circle at 78% 20%,#3a3a3a 0,#1f1f1f 45%,#121212 100%)}
.hero-book{position:absolute;left:200px;top:48px;width:250px;height:520px;background:linear-gradient(100deg,#ddd 0,#fff 18%,#f3f3f3 100%);box-shadow:14px 16px 30px rgba(0,0,0,.5)}
.hero-copy{position:absolute;left:700px;top:160px;color:var(--white)}
.hero-copy h1{font-size:46px;font-weight:800;letter-spacing:1px}
.hero-copy p{font-family:"Montserrat",Arial,sans-serif;font-size:22px;font-weight:700;line-height:1.4;margin-top:12px;width:420px}
.hero-actions{display:flex;gap:22px;margin-top:36px}
.btn{display:inline-block;font-size:14px;font-weight:700;text-transform:uppercase;padding:14px 26px;text-decoration:none;letter-spacing:.5px}
.btn-outline{border:2px solid var(--orange);color:var(--orange)}
.btn-solid{background:var(--orange);color:var(--white);border:2px solid var(--orange)}
.dots{position:absolute;left:568px;top:508px;display:flex;gap:8px}
.dots i{width:20px;height:3px;background:#777;display:block}
.dots i:first-child{background:var(--orange)}
.hero-edge{position:absolute;left:0;top:580px}

/* episodes */
.episodes{position:absolute;top:860px;left:0;width:1200px}
.section-title{text-align:center;font-size:38px;font-weight:800;text-transform:uppercase;letter-spacing:.5px}
.section-title em{font-style:normal;color:var(--orange)}
.cards{position:absolute;top:100px;left:108px;display:flex;gap:12px}
.card{width:320px;height:600px;background:var(--blush);clip-path:polygon(0 0,100% 0,100% 88%,50% 100%,0 88%);text-align:center;position:relative}
.card.featured{background:var(--white);box-shadow:inset 0 0 0 2px var(--line)}
.card-photo{height:224px;background:linear-gradient(180deg,#c9ccd0,#8e949a)}
.badge{width:64px;height:64px;border-radius:50%;background:var(--orange);border:5px solid var(--white);margin:-32px auto 0;position:relative}
.card h4{font-size:15px;font-weight:700;margin-top:14px}
.card h3{font-size:21px;font-weight:800;line-height:1.25;margin:6px 30px 0}
.card p{font-size:14px;color:var(--muted);line-height:1.5;margin:14px 40px 0}
.card .btn{margin-top:26px;padding:12px 26px}
.card.featured .btn{background:var(--white);color:var(--ink);border:2px solid var(--orange)}

/* book banner */
.book-banner{position:absolute;top:1672px;left:0;width:1200px;height:548px;background:linear-gradient(135deg,var(--orange) 0,var(--orange-deep) 100%)}
.banner-photo{position:absolute;left:112px;top:48px;width:468px;height:440px;background:linear-gradient(160deg,#d6dade,#8b9197);border:6px solid var(--white)}
.banner-copy{position:absolute;left:626px;top:96px;width:470px;color:var(--white)}
.banner-copy h2{font-size:40px;font-weight:800;text-transform:uppercase}
.banner-copy h2 span{color:var(--ink)}
.banner-copy p{font-size:15px;line-height:1.75;margin-top:18px}
.banner-copy .btn{margin-top:26px;border:2px solid var(--white);color:var(--white);padding:10px 18px}

/* newsletter */
.newsletter{position:absolute;top:2336px;left:120px;width:680px;height:320px;background:var(--white);box-shadow:0 6px 22px rgba(0,0,0,.14);padding:34px 36px}
.newsletter h2{font-size:34px;font-weight:800;text-transform:uppercase}
.newsletter h2 em{font-style:normal;color:var(--orange)}
.newsletter p{font-size:14px;color:var(--muted);line-height:1.6;margin-top:12px;width:560px}
.fields{display:flex;gap:20px;margin-top:28px}
.fields span{width:270px;height:46px;border:1px solid #cfcfcf;font-size:13px;color:#888;padding:14px}
.newsletter .btn{margin-top:22px;padding:12px 22px}
.news-book{position:absolute;left:880px;top:2344px;width:184px;height:304px;background:linear-gradient(105deg,#b8330f 0,var(--orange) 14%,#f36a40 100%);box-shadow:12px 14px 24px rgba(0,0,0,.3)}

/* footer */
.footer-edge{position:absolute;top:2760px;left:0}
.site-footer{position:absolute;top:2840px;left:0;width:1200px;height:392px;background:var(--footer);color:#cfcfcf}
.col{position:absolute;top:20px;font-size:14px;line-height:1.9}
.col h4{color:var(--white);font-size:16px;font-weight:700;text-transform:uppercase;margin-bottom:10px}
.col.info{left:112px}
.col.contact{left:352px;width:260px}
.col.contact li{display:flex;gap:10px;line-height:1.5;margin-bottom:14px}
.col.contact li::before{content:"";width:8px;height:8px;border-radius:50%;background:var(--orange);margin-top:6px;flex:none}
.col.about{left:660px;width:200px;line-height:1.6}
.col ul{list-style:none}
.footer-brand{position:absolute;left:920px;top:10px;width:200px;text-align:center}
.footer-brand .mark{width:100px;height:100px;border-radius:50%;background:var(--orange);margin:0 auto;display:flex;align-items:center;justify-content:center;font-family:"Montserrat",Arial,sans-serif;color:var(--white);font-weight:800;font-size:15px;line-height:1.1}
.footer-brand .socials{position:static;justify-content:center;margin-top:22px}
.footer-brand .socials i{background:var(--orange);border-color:var(--orange)}
.copyright{position:absolute;left:0;bottom:20px;width:1200px;text-align:center;font-size:13px;color:#bbb}
</style>
</head>
<body>

<header class="site-header">
  <div class="brand">BRIGHT<br>GATHERINGS</div>
  <div class="top-contact">
    <span><svg width="16" height="16" viewBox="0 0 24 24"><path fill="#f04e23" d="M6.6 10.8a15 15 0 0 0 6.6 6.6l2.2-2.2c.3-.3.7-.4 1-.2 1.1.4 2.3.6 3.6.6.6 0 1 .4 1 1V20c0 .6-.4 1-1 1A17 17 0 0 1 3 4c0-.6.4-1 1-1h3.5c.6 0 1 .4 1 1 0 1.3.2 2.5.6 3.6.1.3 0 .7-.2 1z"/></svg>+1 555 014 2290</span>
    <span><svg width="18" height="14" viewBox="0 0 18 14"><rect x="1" y="1" width="16" height="12" fill="none" stroke="#f04e23" stroke-width="2"/><path d="M1 1l8 6 8-6" fill="none" stroke="#f04e23" stroke-width="2"/></svg>info@brightgatherings.example</span>
  </div>
  <div class="socials"><i></i><i></i><i></i><i></i><i class="search"></i></div>
  <nav class="nav">
    <a class="active" href="#">Home</a><a href="#">About us</a><a href="#">Episodes</a><a href="#">Meet the hosts</a><a href="#">Contact us</a>
  </nav>
</header>

<section class="hero">
  <div class="hero-book" role="img" aria-label="Bright Gatherings book cover mockup standing upright"></div>
  <div class="hero-copy">
    <h1>BRIGHT GATHERINGS</h1>
    <p>Lorem Ipsum is simply dummy text of the printing and typesetting industry</p>
    <div class="hero-actions">
      <a class="btn btn-outline" href="#">Get the book now</a>
      <a class="btn btn-solid" href="#">Get trained</a>
    </div>
  </div>
  <div class="dots"><i></i><i></i><i></i><i></i></div>
  <svg class="hero-edge" width="1200" height="130" viewBox="0 0 1200 130">
    <polygon points="0,20 620,110 1200,40 1200,130 0,130" fill="#ffffff"/>
    <polygon points="0,20 620,110 1200,40 1200,52 620,124 0,40" fill="#f04e23"/>
  </svg>
</section>

<section class="episodes">
  <h2 class="section-title">Latest <em>Podcast</em> Episodes</h2>
  <div class="cards">
    <article class="card">
      <div class="card-photo" role="img" aria-label="Portrait photo of the episode guest"></div>
      <div class="badge"></div>
      <h4>Episode 195:</h4>
      <h3>There are many variations of passages</h3>
      <p>Lorem Ipsum is simply dummy text typesetting industry.</p>
      <a class="btn btn-solid" href="#">Explore</a>
    </article>
    <article class="card featured">
      <div class="card-photo" role="img" aria-label="Portrait photo of the episode guest"></div>
      <div class="badge"></div>
      <h4>Episode 195:</h4>
      <h3>There are many variations of passages</h3>
      <p>Lorem Ipsum is simply dummy text typesetting industry.</p>
      <a class="btn" href="#">Explore</a>
    </article>
    <article class="card">
      <div class="card-photo" role="img" aria-label="Portrait photo of the episode guest"></div>
      <div class="badge"></div>
      <h4>Episode 195:</h4>
      <h3>There are many variations of passages</h3>
      <p>Lorem Ipsum is simply dummy text typesetting industry.</p>
      <a class="btn btn-solid" href="#">Explore</a>
    </article>
  </div>
</section>

<section class="book-banner">
  <div class="banner-photo" role="img" aria-label="Facilitator presenting to a seated group in a bright meeting room"></div>
  <div class="banner-copy">
    <h2>Bright <span>Gathering</span></h2>
    <p>It is a long established fact that a reader will be distracted by the readable content of a page when looking at its layout. The point of using Lorem Ipsum is that it has a more-or-less normal distribution of letters, as opposed to using 'Content here, content here', making it look like readable English.</p>
    <a class="btn" href="#">Read more ›</a>
  </div>
</section>

<section class="newsletter">
  <h2>Subscribe to the <em>Newsletter</em></h2>
  <p>It is a long established fact that a reader will be distracted by the readable content of a page when looking at its layout.</p>
  <div class="fields"><span>Your Name</span><span>Your Email</span></div>
  <a class="btn btn-solid" href="#">Subscribe</a>
</section>
<div class="news-book" role="img" aria-label="Orange Bright Gatherings book cover mockup"></div>

<svg class="footer-edge" width="1200" height="82" viewBox="0 0 1200 82">
  <polygon points="0,82 0,52 420,0 1200,60 1200,82" fill="#f04e23"/>
  <polygon points="0,82 0,66 420,14 1200,74 1200,82" fill="#0b0b0b"/>
</svg>
<footer class="site-footer">
  <div class="col info">
    <h4>Information</h4>
    <ul><li>Home</li><li>About us</li><li>Episodes</li><li>Meet the hosts</li><li>Contact us</li></ul>
  </div>
  <div class="col contact">
    <h4>Contact us</h4>
    <ul>
      <li>Lorem Ipsum is simply typesetting industry</li>
      <li>+1 555 014 2290</li>
      <li>info@brightgatherings.example</li>
    </ul>
  </div>
  <div class="col about">
    <h4>About us</h4>
    <p>It is a long established fact that a reader will be distracted by the readable content of a page when looking at its layout.</p>
  </div>
  <div class="footer-brand">
    <div class="mark">BRIGHT<br>GATHERINGS</div>
    <div class="socials"><i></i><i></i><i></i><i></i></div>
  </div>
  <p class="copyright">© Copyrights 2019 | All Rights are Reserved</p>
</footer>

</body>
</html>
```